Boutique Technology Consultancy specialising is Electronic and physical security

We need to redo our existing outdated website. For your reference the link www.pelu.com.au

```html
<!DOCTYPE html>
<html lang="en">
<head>
<meta charset="utf-8">
<title>PELU Services</title>
<link href="https://fonts.googleapis.com/css2?family=Montserrat:wght@400;500;600;700;800&display=swap" rel="stylesheet">
<style>
:root{
  --bg:#050505;
  --red:#d8232a;
  --red-dark:#8e0d12;
  --red-bright:#f2333b;
  --white:#ffffff;
  --grey:#bdbdbd;
  --field:#9a9a9a;
}
*{margin:0;padding:0;box-sizing:border-box}
html,body{width:1200px;height:4000px;overflow:hidden}
body{background:var(--bg);color:var(--white);font-family:'Montserrat',sans-serif;position:relative}
.abs{position:absolute}
.center{left:0;width:1200px;text-align:center}

/* header */
.brand{display:flex;align-items:center;gap:14px}
.brand-mark{width:26px;height:26px;background:var(--red)}
.brand-name{font-weight:700;font-size:60px;letter-spacing:1px;color:var(--white);line-height:1}
.nav{top:61px;left:512px;display:flex;gap:29px;font-weight:700;font-size:14px}
.nav a{color:var(--white);text-decoration:none}
.nav .active::before{content:"";display:inline-block;width:0;height:0;border-top:4px solid transparent;border-bottom:4px solid transparent;border-right:7px solid var(--red);margin-right:5px;vertical-align:1px}

/* hero */
.hero-title{top:218px;left:146px;font-weight:800;font-size:45px;line-height:59px;letter-spacing:.5px}
.btn{display:flex;align-items:center;justify-content:center;background:var(--red);color:var(--white);font-weight:700;font-size:13px;text-decoration:none}
.btn-dark{background:#0b0b0b}
.hero-btn{top:478px;left:146px;width:164px;height:50px}
.dots{top:600px;left:144px;display:flex;gap:12px}
.dots span{width:8px;height:8px;border-radius:50%;background:var(--white)}
.dots span:first-child{background:var(--red)}

/* section headings */
.section-title{font-weight:800;font-size:46px;letter-spacing:.5px;display:flex;align-items:center;justify-content:center;gap:18px}
.section-title::before,.section-title::after{content:"";width:34px;height:3px;background:var(--red)}
.lead{font-size:14.5px;line-height:27px;font-weight:500}

/* experience */
.project{width:260px;text-align:center}
.project svg{display:block;margin:0 auto}
.project-name{margin-top:18px;font-weight:700;font-size:21px;line-height:28px}

/* ticks */
.ticks{display:flex;justify-content:center;gap:36px;font-weight:700;font-size:17px}
.ticks span{display:flex;align-items:center;gap:9px}

/* team */
.member{width:300px;text-align:center}
.member-name{font-weight:700;font-size:14.5px;margin-top:16px}
.member-bio{font-size:14px;line-height:25px;margin-top:12px;font-weight:500}

/* contact */
.contact-item{display:flex;align-items:center;gap:16px;font-weight:700;font-size:19px;line-height:25px}
.field{border:1.5px solid var(--field);background:transparent;color:var(--white);font-size:11px;padding:18px 22px 0;font-weight:500}

/* footer */
.footer-text{font-size:14px;line-height:20px;font-weight:500}
.social{display:flex;gap:14px}
.social span{width:30px;height:30px;border-radius:50%;background:var(--red)}
</style>
</head>
<body>

<header>
  <div class="abs brand" style="top:38px;left:146px">
    <span class="brand-mark"></span><span class="brand-name">PELU</span>
  </div>
  <nav class="abs nav">
    <a class="active" href="#">HOME</a><a href="#">EXPERIENCE</a><a href="#">SERVICES</a><a href="#">TEAM</a><a href="#">ABOUT</a><a href="#">CONTACT</a>
  </nav>
</header>

<section class="hero">
  <h1 class="abs hero-title">YOUR<br>TECHNOLOGY<br>PROJECTS<br>MADE EASY</h1>
  <a class="abs btn hero-btn" href="#">GET STARTED</a>
  <div class="abs dots"><span></span><span></span><span></span><span></span></div>
  <svg class="abs" style="top:150px;left:500px" width="700" height="480" viewBox="0 0 700 480">
    <defs>
      <linearGradient id="heroPhoto" x1="0" y1="0" x2="1" y2="1">
        <stop offset="0" stop-color="#6a6f78"/><stop offset=".5" stop-color="#c9cfd8"/><stop offset="1" stop-color="#3b3f48"/>
      </linearGradient>
      <linearGradient id="heroArt" x1="0" y1="0" x2="0" y2="1">
        <stop offset="0" stop-color="#c61d24"/><stop offset="1" stop-color="#4a0507" stop-opacity=".2"/>
      </linearGradient>
    </defs>
    <polygon role="img" aria-label="Photo of a woman reviewing data charts on a laptop" points="146,5 556,5 556,453 146,453 4,229" fill="url(#heroPhoto)"/>
    <polyline points="146,5 4,229 146,453" fill="none" stroke="var(--red)" stroke-width="6"/>
    <rect role="img" aria-label="Decorative red artwork" x="556" y="0" width="144" height="470" fill="url(#heroArt)"/>
  </svg>
</section>

<section class="experience">
  <h2 class="abs center section-title" style="top:712px">EXPERIENCE</h2>
  <p class="abs center lead" style="top:787px">PELU has a diverse range of project experience across a range of industries within both the public and<br>private sectors. The following is a small sample of some of the clients and sites we have worked with.</p>

  <div class="abs project" style="top:888px;left:159px">
    <svg width="260" height="264" viewBox="0 0 260 264"><defs><linearGradient id="p1" x1="0" y1="0" x2="0" y2="1"><stop offset="0" stop-color="#d8d8d8"/><stop offset="1" stop-color="#3a3a3a"/></linearGradient></defs>
    <polygon role="img" aria-label="Black and white photo of a historic tower under a glass cone" points="130,2 258,132 130,262 2,132" fill="url(#p1)"/><polyline points="2,132 130,262 258,132" fill="none" stroke="var(--red)" stroke-width="5"/></svg>
    <div class="project-name">Harbourline<br>Plaza</div>
  </div>
  <div class="abs project" style="top:888px;left:471px">
    <svg width="260" height="264" viewBox="0 0 260 264"><defs><linearGradient id="p2" x1="0" y1="0" x2="0" y2="1"><stop offset="0" stop-color="#e6e6e6"/><stop offset="1" stop-color="#2e2e2e"/></linearGradient></defs>
    <polygon role="img" aria-label="Black and white photo of a toll road gantry over a motorway" points="130,2 258,132 130,262 2,132" fill="url(#p2)"/><polyline points="2,132 130,262 258,132" fill="none" stroke="var(--red)" stroke-width="5"/></svg>
    <div class="project-name">Northway</div>
  </div>
  <div class="abs project" style="top:888px;left:782px">
    <svg width="260" height="264" viewBox="0 0 260 264"><defs><linearGradient id="p3" x1="0" y1="0" x2="0" y2="1"><stop offset="0" stop-color="#cfcfcf"/><stop offset="1" stop-color="#333"/></linearGradient></defs>
    <polygon role="img" aria-label="Black and white photo of a hospital atrium with stairs" points="130,2 258,132 130,262 2,132" fill="url(#p3)"/><polyline points="2,132 130,262 258,132" fill="none" stroke="var(--red)" stroke-width="5"/></svg>
    <div class="project-name">Crestmoor<br>Hospital</div>
  </div>

  <div class="abs project" style="top:1248px;left:159px">
    <svg width="260" height="264" viewBox="0 0 260 264"><defs><linearGradient id="p4" x1="0" y1="0" x2="1" y2="1"><stop offset="0" stop-color="#e0e0e0"/><stop offset="1" stop-color="#1f1f1f"/></linearGradient></defs>
    <polygon role="img" aria-label="Black and white photo of glass office towers" points="130,2 258,132 130,262 2,132" fill="url(#p4)"/><polyline points="2,132 130,262 258,132" fill="none" stroke="var(--red)" stroke-width="5"/></svg>
    <div class="project-name">Kestrel Towers</div>
  </div>
  <div class="abs project" style="top:1248px;left:471px">
    <svg width="260" height="264" viewBox="0 0 260 264"><defs><linearGradient id="p5" x1="0" y1="0" x2="0" y2="1"><stop offset="0" stop-color="#c4c4c4"/><stop offset="1" stop-color="#303030"/></linearGradient></defs>
    <polygon role="img" aria-label="Black and white photo of a bank building entrance" points="130,2 258,132 130,262 2,132" fill="url(#p5)"/><polyline points="2,132 130,262 258,132" fill="none" stroke="var(--red)" stroke-width="5"/></svg>
    <div class="project-name">Southern Union<br>Bank</div>
  </div>
  <div class="abs project" style="top:1248px;left:782px">
    <svg width="260" height="264" viewBox="0 0 260 264"><defs><linearGradient id="p6" x1="1" y1="0" x2="0" y2="1"><stop offset="0" stop-color="#bdbdbd"/><stop offset="1" stop-color="#262626"/></linearGradient></defs>
    <polygon role="img" aria-label="Black and white photo of a mother and child" points="130,2 258,132 130,262 2,132" fill="url(#p6)"/><polyline points="2,132 130,262 258,132" fill="none" stroke="var(--red)" stroke-width="5"/></svg>
    <div class="project-name">Safe Homes<br>Trust</div>
  </div>

  <a class="abs btn" style="top:1626px;left:517px;width:165px;height:50px" href="#">VIEW MORE</a>
</section>

<section class="services">
  <svg class="abs" style="top:1752px;left:0" width="1200" height="340" viewBox="0 0 1200 340">
    <defs>
      <linearGradient id="servicesBand" x1="0" y1="0" x2="1" y2="0">
        <stop offset="0" stop-color="#b3141b"/><stop offset=".4" stop-color="var(--red-bright)"/><stop offset="1" stop-color="#8e0d12"/>
      </linearGradient>
    </defs>
    <polygon points="143,0 1056,0 1200,170 1056,340 143,340 0,170" fill="url(#servicesBand)"/>
    <path d="M760,0 C820,120 1000,200 1200,170 L1056,340 L900,340 C960,220 900,90 760,0 Z" fill="var(--red-dark)" opacity=".55"/>
    <path d="M40,120 C200,280 520,290 740,170" fill="none" stroke="#ff5b61" stroke-width="2" opacity=".35"/>
  </svg>
  <h2 class="abs center section-title" style="top:1786px">SERVICES</h2>
  <p class="abs center lead" style="top:1862px">PELU Services provides independent professional services for projects as well as operations and<br>maintenance. We offer end to end services including:</p>
  <div class="abs center ticks" style="top:1939px">
    <span><svg width="20" height="20" viewBox="0 0 20 20"><circle cx="9" cy="11" r="7.5" fill="none" stroke="#fff" stroke-width="2"/><path d="M5.5,10.5 9,14 18,3" fill="none" stroke="#fff" stroke-width="2.4"/></svg>Strategy</span>
    <span><svg width="20" height="20" viewBox="0 0 20 20"><circle cx="9" cy="11" r="7.5" fill="none" stroke="#fff" stroke-width="2"/><path d="M5.5,10.5 9,14 18,3" fill="none" stroke="#fff" stroke-width="2.4"/></svg>Design</span>
    <span><svg width="20" height="20" viewBox="0 0 20 20"><circle cx="9" cy="11" r="7.5" fill="none" stroke="#fff" stroke-width="2"/><path d="M5.5,10.5 9,14 18,3" fill="none" stroke="#fff" stroke-width="2.4"/></svg>Operations and maintenance</span>
  </div>
  <a class="abs btn btn-dark" style="top:1997px;left:517px;width:165px;height:50px" href="#">VIEW MORE</a>
</section>

<section class="team">
  <h2 class="abs center section-title" style="top:2186px">OUR TEAM</h2>

  <div class="abs member" style="top:2290px;left:113px">
    <svg width="160" height="156" viewBox="0 0 160 156"><polygon points="100,4 142,0 128,50" fill="var(--red)"/><polygon points="8,70 26,60 24,82" fill="var(--red)"/><circle role="img" aria-label="Portrait of Rob Carter" cx="80" cy="82" r="70" fill="#8a7a6c"/></svg>
    <div class="member-name">Rob Carter - Principal Consultant</div>
    <p class="member-bio">Rob founded PELU in 2016 and<br>continues to lead the organisation<br>nationally.</p>
  </div>
  <div class="abs member" style="top:2290px;left:450px">
    <svg width="160" height="156" viewBox="0 0 160 156"><polygon points="100,4 142,0 128,50" fill="var(--red)"/><polygon points="8,70 26,60 24,82" fill="var(--red)"/><circle role="img" aria-label="Portrait of Sam Hollis" cx="80" cy="82" r="70" fill="#9b8f86"/></svg>
    <div class="member-name">Sam Hollis - Principal Consultant</div>
    <p class="member-bio">Sam founded Vantage Systems in 2016<br>and joined PELU as a Director in<br>2022, taking over leadership of the<br>NSW office.</p>
  </div>
  <div class="abs member" style="top:2290px;left:786px">
    <svg width="160" height="156" viewBox="0 0 160 156"><polygon points="100,4 142,0 128,50" fill="var(--red)"/><polygon points="8,70 26,60 24,82" fill="var(--red)"/><circle role="img" aria-label="Portrait of Daniel Garrow" cx="80" cy="82" r="70" fill="#7d6a5e"/></svg>
    <div class="member-name">Daniel Garrow - Senior Consultant</div>
    <p class="member-bio">Daniel established PELU's<br>Queensland office in 2019 and leads<br>all of PELU's engagements in the<br>northern states.</p>
  </div>

  <a class="abs btn" style="top:2637px;left:517px;width:165px;height:50px" href="#">VIEW MORE</a>
</section>

<section class="about">
  <svg class="abs" style="top:2756px;left:0" width="1200" height="340" viewBox="0 0 1200 340">
    <defs>
      <linearGradient id="aboutBand" x1="0" y1="0" x2="1" y2="1">
        <stop offset="0" stop-color="#1c1c1c"/><stop offset=".5" stop-color="#2b2b2b"/><stop offset="1" stop-color="#111"/>
      </linearGradient>
    </defs>
    <polygon points="143,2 1056,2 1198,170 1056,338 143,338 2,170" fill="url(#aboutBand)" stroke="var(--red)" stroke-width="3"/>
    <polygon points="440,338 640,100 820,338" fill="#000" opacity=".25"/>
    <polygon points="200,2 420,2 300,160" fill="#3a3a3a" opacity=".25"/>
  </svg>
  <h2 class="abs center section-title" style="top:2790px">ABOUT</h2>
  <p class="abs center lead" style="top:2863px">PELU Services was established in 2016 by Rob Carter to provide technology consulting services to corporate<br>and government clients with a focus on:</p>
  <div class="abs center ticks" style="top:2940px">
    <span><svg width="20" height="20" viewBox="0 0 20 20"><circle cx="9" cy="11" r="7.5" fill="none" stroke="#fff" stroke-width="2"/><path d="M5.5,10.5 9,14 18,3" fill="none" stroke="#fff" stroke-width="2.4"/></svg>Property/facilities management</span>
    <span><svg width="20" height="20" viewBox="0 0 20 20"><circle cx="9" cy="11" r="7.5" fill="none" stroke="#fff" stroke-width="2"/><path d="M5.5,10.5 9,14 18,3" fill="none" stroke="#fff" stroke-width="2.4"/></svg>Asset management</span>
    <span><svg width="20" height="20" viewBox="0 0 20 20"><circle cx="9" cy="11" r="7.5" fill="none" stroke="#fff" stroke-width="2"/><path d="M5.5,10.5 9,14 18,3" fill="none" stroke="#fff" stroke-width="2.4"/></svg>Development and Construction</span>
  </div>
  <a class="abs btn" style="top:2999px;left:515px;width:168px;height:50px" href="#">READ MORE</a>
</section>

<section class="contact">
  <h2 class="abs center section-title" style="top:3183px">CONTACT</h2>

  <div class="abs contact-item" style="top:3291px;left:178px">
    <svg width="74" height="74" viewBox="0 0 74 74"><polygon points="37,3 71,37 37,71 3,37" fill="none" stroke="var(--red)" stroke-width="3"/><rect x="26" y="29" width="22" height="15" fill="#fff"/><path d="M26,29 37,38 48,29" fill="none" stroke="#050505" stroke-width="2"/></svg>
    <span>hello@pelu.com.au</span>
  </div>
  <div class="abs contact-item" style="top:3291px;left:482px">
    <svg width="74" height="74" viewBox="0 0 74 74"><polygon points="37,3 71,37 37,71 3,37" fill="var(--red)"/><path d="M37,49 C30,40 28,36 28,32 a9,9 0 0 1 18,0 C46,36 44,40 37,49Z" fill="#fff"/><circle cx="37" cy="32" r="3.5" fill="var(--red)"/></svg>
    <span>PO Box 4120<br>MELBOURNE VIC 3000</span>
  </div>
  <div class="abs contact-item" style="top:3291px;left:816px">
    <svg width="74" height="74" viewBox="0 0 74 74"><polygon points="37,3 71,37 37,71 3,37" fill="none" stroke="var(--red)" stroke-width="3"/><path d="M31,29 c-2,1 -2,4 0,7 c3,5 6,8 10,10 c3,1 5,0 6,-2 l-3,-3 c-1,-1 -2,0 -3,1 c-2,-1 -5,-4 -6,-6 c1,-1 2,-2 1,-3 Z" fill="#fff"/></svg>
    <span>1300 555 014</span>
  </div>

  <div class="abs field" style="top:3426px;left:255px;width:338px;height:50px">Enter Name</div>
  <div class="abs field" style="top:3426px;left:607px;width:338px;height:50px">Enter Email</div>
  <div class="abs field" style="top:3494px;left:255px;width:338px;height:50px">Phone</div>
  <div class="abs field" style="top:3494px;left:607px;width:338px;height:50px">Address</div>
  <div class="abs field" style="top:3561px;left:255px;width:690px;height:130px">Message</div>
  <a class="abs btn" style="top:3718px;left:517px;width:165px;height:48px" href="#">SUBMIT</a>
</section>

<footer>
  <div class="abs brand" style="top:3855px;left:153px">
    <span class="brand-mark"></span><span class="brand-name">PELU</span>
  </div>
  <p class="abs footer-text" style="top:3842px;left:528px">© 2023 PELU Services Pty Ltd All rights reserved &nbsp;|&nbsp; Privacy &nbsp;|&nbsp; Terms of Use</p>
  <p class="abs footer-text" style="top:3875px;left:532px">ABN: 12 345 678 901</p>
  <div class="abs social" style="top:3914px;left:529px"><span></span><span></span></div>
</footer>

</body>
</html>
```